Rebrand stationary with recently completed logo design

Need new business cards, thank you cards, letterhead, envelopes and presentation folders. The designs will be sent to a separate production firm so I need the files to be print ready.

My contact info
Reko Haliburn

Office 604-318-5047
Fax 604-371-8054

Email reko@glazemark.ca
website www.glazemark.ca

315-14720 62nd Avenue,
Langley, BC, V2K 3R8

Target Market(s)

Homeowners, businesses and contractors

Industry/Entity Type

Business

Font styles to use
Sans Serif

Colors
34a7d7

Requirements
Must have
• Like to have one side of the business card a solid color with the logo in all white. The side with all the text to be a white background
• I find the current blue on the front of the card with the white logo too dark.
Should not have
• Gradient colors

```html
<!DOCTYPE html>
<html lang="en">
<head>
<meta charset="utf-8">
<title>Glazemark Envelope</title>
<link href="https://fonts.googleapis.com/css2?family=Fira+Sans:ital,wght@0,300;0,400;1,300&display=swap" rel="stylesheet">
<style>
  :root {
    --brand-blue: #2ea4d8;
    --slate: #4b555e;
    --ink: #5a5f64;
    --paper: #ffffff;
  }
  html, body {
    margin: 0;
    padding: 0;
    width: 1200px;
    height: 512px;
    overflow: hidden;
    background: var(--paper);
  }
  .envelope {
    position: relative;
    width: 1200px;
    height: 512px;
    box-sizing: border-box;
    border: 1px solid var(--brand-blue);
    background: var(--paper);
    font-family: "Fira Sans", sans-serif;
  }
  .brand-mark {
    position: absolute;
    left: 152px;
    top: 42px;
    width: 52px;
    height: 52px;
    background: var(--slate);
  }
  .brand-name {
    position: absolute;
    left: 46px;
    top: 142px;
    margin: 0;
    font-family: "Fira Sans", sans-serif;
    font-weight: 400;
    font-size: 45px;
    line-height: 1;
    letter-spacing: 0.5px;
    color: var(--brand-blue);
  }
  .return-address {
    position: absolute;
    left: 46px;
    top: 414px;
    margin: 0;
    font-family: "Fira Sans", sans-serif;
    font-style: italic;
    font-weight: 300;
    font-size: 21px;
    line-height: 32px;
    color: var(--ink);
  }
  .return-address .label {
    color: var(--brand-blue);
    font-weight: 400;
  }
  .return-address .divider {
    color: var(--ink);
    margin: 0 4px;
  }
</style>
</head>
<body>
  <main class="envelope">
    <div class="brand-mark" aria-hidden="true"></div>
    <h1 class="brand-name">GLAZEMARK</h1>
    <address class="return-address">
      <span class="contact-line"><span class="label">p</span> 604-318-5047<span class="divider">|</span><span class="label">f</span> 604-371-8054<span class="divider">|</span><span class="label">e</span> reko@glazemark.ca</span><br>
      <span class="contact-line"><span class="label">#</span>315-14720 62nd Avenue, Langley, BC, V2K 3R8</span>
    </address>
  </main>
</body>
</html>
```